Veltrano.co - Polar Expeditions Specialists

We need a modern, visually striking business card for Veltrano.co, a company specialized in selling expedition cruises to the most remote regions on Earth, with a focus on the Arctic and Antarctica. The design should instantly communicate that the cardholder is an expert in polar travel. Use clean, premium aesthetics with cool tones like icy blue and white, possibly incorporating polar imagery (ice, glaciers, penguins, etc.)

Attached the logo

Contact Information for Business Card

Feels high-end and trustworthy.. Visually memorable — encourages people to keep it

Colors
0054AA
0677BA
7BADD7
CADEEF
E8F1F8

Requirements
Must have
• ice, glaciers, penguins, montains
Nice to have
• modern, transparente,

```html
<!DOCTYPE html>
<html lang="en">
<head>
<meta charset="utf-8">
<title>Veltrano.co – Business Card</title>
<link href="https://fonts.googleapis.com/css2?family=Poppins:wght@400;500;600;700&display=swap" rel="stylesheet">
<style>
  :root {
    --stage: #2a2b30;
    --card-navy: #111230;
    --faint-navy: #1b2142;
    --polar-blue: #3575b5;
    --brand-blue: #3d83c8;
    --ice-white: #ffffff;
    --text-soft: #e8f1f8;
  }
  * { margin: 0; padding: 0; box-sizing: border-box; }
  html, body {
    width: 1200px; height: 900px; overflow: hidden;
    background: var(--stage);
    font-family: "Poppins", sans-serif;
  }
  .stage {
    position: relative; width: 1200px; height: 900px;
    display: flex; flex-direction: column; align-items: center; justify-content: center; gap: 30px;
  }
  .card {
    position: relative; width: 720px; height: 410px;
    background: var(--card-navy); border-radius: 22px; overflow: hidden;
    box-shadow: 0 14px 30px rgba(0,0,0,.45);
  }

  /* Front */
  .front-decoration {
    position: absolute; right: 50px; top: 70px; width: 270px; height: 340px;
    background: var(--faint-navy); border-radius: 120px 120px 0 0;
  }
  .front-brand {
    position: absolute; left: 0; right: 0; top: 110px; text-align: center; color: var(--ice-white);
  }
  .front-brand .brand-dot {
    display: block; width: 46px; height: 46px; margin: 0 auto 16px;
    border-radius: 50%; background: var(--ice-white);
  }
  .front-brand .brand-name { font-weight: 700; font-size: 78px; line-height: 1; letter-spacing: 1px; }
  .front-brand .brand-tagline { font-weight: 500; font-size: 21px; margin-top: 10px; letter-spacing: .5px; }

  /* Back */
  .back-illustration {
    position: absolute; left: 20px; top: 60px; width: 290px; height: 360px;
    background: linear-gradient(180deg, #3a7cbd, var(--polar-blue));
    border-radius: 140px 160px 0 0;
  }
  .back-info { position: absolute; left: 340px; top: 70px; width: 360px; }
  .back-brand { display: flex; align-items: center; gap: 12px; color: var(--brand-blue); }
  .back-brand .brand-dot { width: 34px; height: 34px; border-radius: 50%; background: var(--brand-blue); flex: none; }
  .back-brand .brand-name { font-weight: 700; font-size: 48px; line-height: 1; }
  .back-brand-tagline { color: var(--brand-blue); font-weight: 600; font-size: 14px; margin: 6px 0 0 46px; }
  .holder-name { color: var(--brand-blue); font-weight: 700; font-size: 28px; margin-top: 28px; line-height: 1.1; }
  .holder-role { color: var(--text-soft); font-size: 15px; margin-top: 2px; }
  .holder-address { color: var(--text-soft); font-size: 15px; line-height: 1.4; margin-top: 18px; }
  .contact-list { list-style: none; margin-top: 16px; color: var(--text-soft); font-size: 15px; }
  .contact-list li { display: flex; align-items: center; gap: 10px; line-height: 1.55; }
  .contact-list svg { width: 13px; height: 13px; fill: var(--brand-blue); flex: none; }
</style>
</head>
<body>
<main class="stage">
  <section class="card card-front">
    <div class="front-decoration" role="img" aria-label="Faint polar bear and penguin silhouette decoration"></div>
    <div class="front-brand">
      <span class="brand-dot"></span>
      <div class="brand-name">Veltrano.co</div>
      <div class="brand-tagline">Polar Expeditions Specialists</div>
    </div>
  </section>

  <section class="card card-back">
    <div class="back-illustration" role="img" aria-label="Large blue polar bear silhouette with penguins and a star"></div>
    <div class="back-info">
      <div class="back-brand"><span class="brand-dot"></span><span class="brand-name">Veltrano.co</span></div>
      <div class="back-brand-tagline">Polar Expeditions Specialists</div>
      <div class="holder-name">Marlo Quint</div>
      <div class="holder-role">CEO &amp; Founder</div>
      <div class="holder-address">42 Harbor Point Lane,<br>Eastbrook, ME 04011 USA</div>
      <ul class="contact-list">
        <li><svg viewBox="0 0 16 16"><path d="M3 1h3l1.5 4-2 1.2a9 9 0 0 0 4.3 4.3L11 8.5l4 1.5v3a2 2 0 0 1-2 2A12 12 0 0 1 1 3a2 2 0 0 1 2-2z"/></svg>+1.555.010.274</li>
        <li><svg viewBox="0 0 16 16"><path d="M1 3h14v10H1z M1 3l7 6 7-6" /></svg>hello@veltranomail.com</li>
        <li><svg viewBox="0 0 16 16"><circle cx="8" cy="8" r="7"/></svg>www.veltrano-travel.com</li>
      </ul>
    </div>
  </section>
</main>
</body>
</html>
```